Flat bootstrap design for existing site

I'm looking for a modern flat design based around an existing logo. This has to be a custom design (no external templates), and implemented into a bootstrap framework.

The logo is attached as 2 versions - choose whichever you want, that flows better with whatever design you choose.

Added screenshots of the existing site (currently using the default bootstrap layouts). Please make your designs around those pages in the screenshots (i.e. the homepage only has the postal code input and the header). The active page has 3 screenshots, because I wanted to illustrate the other states that would be visible (in the table rows).

This is a moving/junk removal website, just for some context.

Here's some example websites (flat designs) that I like, just to give you an idea of what I'm after.

https://www.plimvora.com/
https://dacklow.com/
https://trevanu.com/
https://quobrintal.com/en/

Coding

Coded - Design and coding required

Number of Pages Required

5+ page

Colors

Designer to choose colors to be used in the design.

Requirements
Must have
• It must be a modern/simple flat design, that is built around the existing logo (attached).
• It has to be implemented using bootstrap.

```html
<!DOCTYPE html>
<html lang="en">
<head>
<meta charset="utf-8">
<title>Haulden — Junk removal on demand</title>
<link rel="stylesheet" href="https://fonts.googleapis.com/css2?family=Montserrat:wght@600;700&family=Raleway:wght@300&family=Roboto:wght@400&display=swap">
<style>
  :root {
    --sky: #38bcf2;
    --sky-light: #5ccaf5;
    --navy-button: #1088cf;
    --violet: #6a5acd;
    --violet-dark: #6451c4;
    --lime: #8dc63f;
    --white: #ffffff;
    --hill: #f5f5f7;
    --hill-blue: #bfe8fa;
    --footer-text: #4a4a6a;
    --social: #8e8aae;
  }
  * { box-sizing: border-box; margin: 0; padding: 0; }
  html, body { width: 1200px; height: 621px; overflow: hidden; background: var(--white); }
  body { position: relative; font-family: "Montserrat", Arial, sans-serif; }

  .hero {
    position: absolute; left: 0; top: 0; width: 1200px; height: 556px;
    background: var(--sky); overflow: hidden;
  }
  .hero-scenery { position: absolute; left: 0; top: 0; }

  .site-header {
    position: absolute; left: 144px; top: 16px; width: 912px; height: 50px;
    display: flex; align-items: center; justify-content: space-between;
  }
  .brand {
    color: var(--white); font-weight: 700; font-size: 30px; letter-spacing: 1px;
    text-decoration: none; display: flex; align-items: center; gap: 8px;
  }
  .brand-dot { width: 14px; height: 14px; border-radius: 50%; background: var(--white); }
  .main-nav { display: flex; align-items: center; }
  .main-nav a {
    color: var(--white); text-decoration: none; font-weight: 600; font-size: 11px;
    letter-spacing: 0.4px;
  }
  .nav-link { margin-right: 26px; }
  .nav-link + .nav-link { margin-right: 24px; }
  .nav-button {
    display: inline-flex; align-items: center; justify-content: center;
    height: 35px; border-radius: 2px;
  }
  .nav-button.driver { width: 135px; background: var(--navy-button); margin-right: 8px; }
  .nav-button.signin { width: 81px; background: var(--violet); }

  .hero-copy {
    position: absolute; left: 237px; top: 176px; width: 480px; text-align: center;
    color: var(--white); font-family: "Raleway", Arial, sans-serif; font-weight: 300;
    font-size: 46px; line-height: 52px;
  }
  .book-button {
    position: absolute; left: 416px; top: 302px; width: 125px; height: 50px;
    background: var(--lime); color: var(--white); text-decoration: none;
    font-weight: 600; font-size: 13px; letter-spacing: 0.5px; border-radius: 2px;
    display: flex; align-items: center; justify-content: center; gap: 10px;
    box-shadow: 0 8px 14px rgba(20, 80, 120, 0.25);
  }

  .site-footer {
    position: absolute; left: 0; top: 556px; width: 1200px; height: 65px;
    border-bottom: 7px solid var(--violet-dark); background: var(--white);
  }
  .copyright {
    position: absolute; left: 144px; top: 25px; font-family: "Roboto", Arial, sans-serif;
    font-size: 12px; color: var(--footer-text);
  }
  .social-links { position: absolute; left: 987px; top: 23px; display: flex; gap: 7px; }
  .social-links a { width: 18px; height: 18px; background: var(--social); border-radius: 2px; display: block; }
</style>
</head>
<body>
  <section class="hero">
    <svg class="hero-scenery" width="1200" height="556" viewBox="0 0 1200 556">
      <path d="M690 556 C720 380 880 160 1200 148 L1200 556 Z" fill="var(--hill)"/>
      <path d="M860 556 C900 420 1040 330 1200 330 L1200 556 Z" fill="var(--hill-blue)" opacity="0.7"/>
      <rect x="790" y="124" width="410" height="305" rx="6" fill="var(--sky-light)" opacity="0.55"
            role="img" aria-label="Illustration of a smiling mover pushing a wheelie bin beside a rubbish bag, houses and a branded van"/>
    </svg>

    <header class="site-header">
      <a class="brand" href="#"><span class="brand-dot"></span>HAULDEN</a>
      <nav class="main-nav">
        <a class="nav-link" href="#">BOOK</a>
        <a class="nav-link" href="#">HOW IT WORKS</a>
        <a class="nav-button driver" href="#">BECOME A DRIVER</a>
        <a class="nav-button signin" href="#">SIGNIN</a>
      </nav>
    </header>

    <h1 class="hero-copy">Need junk removed?<br>Book now.</h1>
    <a class="book-button" href="#">BOOK
      <svg width="16" height="8" viewBox="0 0 16 8"><path d="M0 4 H14 M11 1 L14.5 4 L11 7" stroke="currentColor" stroke-width="1.3" fill="none"/></svg>
    </a>
  </section>

  <footer class="site-footer">
    <p class="copyright">© 2017 HAULDEN. All rights reserved.</p>
    <div class="social-links">
      <a href="#" aria-label="Social profile one"></a>
      <a href="#" aria-label="Social profile two"></a>
      <a href="#" aria-label="Social profile three"></a>
    </div>
  </footer>
</body>
</html>
```